RV7 - Rapid Vigil Field Operations Suite

I need an introductory website for RV7 which describes the features of the product and the ease of use of the product. The product is focused on Preparing for an incident using Volunteer and Resource management and then responding to an incident with Incident Management, Team Management, Task Management and Communication Management. Once a situation is handled, the application provides complete reporting on each of the above aspects

Target Market(s)

Local Government entities, specifically the emergency department directors or coordinators

Industry/Entity Type

Government Office

Coding

Coded - Design and coding required

Font styles to use
Sans Serif

Requirements
Must have
• Clear layout with modern images. I want to be able to get a clear understanding of the features of the product and the ease of use. I would like to high light how the application helps in Communication Management, Team Management, Task Management and Incident Managements. Also, how the use of application helps to get an immediate snap shot of how well an incident was handled. I want to highlight how the Dashboard provides a quick look at the Incident(s) being managed
Nice to have
• I would like to in the future add videos to the site. At this point don't have any ideas about nice to have features
Should not have
• traditional designs. I am looking for a slick, modern looking website. Clean design is the key.

```html
<!DOCTYPE html>
<html lang="en">
<head>
<meta charset="utf-8">
<title>RV7 - Rapid Vigil Field Operations Suite</title>
<link rel="stylesheet" href="https://fonts.googleapis.com/css2?family=Raleway:wght@500;600;700;800&family=Open+Sans:wght@400;600;700&display=swap">
<style>
:root{
  --blue:#2a63b1;
  --navy:#1d3e8a;
  --green:#8cc63f;
  --green-dark:#7ab22f;
  --ink:#222;
  --text:#666;
  --light:#f4f4f4;
  --dark:#2a2a2a;
  --footer:#161616;
  --white:#fff;
}
*{margin:0;padding:0;box-sizing:border-box}
html,body{width:1200px;height:2844px;overflow:hidden;background:var(--white)}
body{position:relative;font-family:"Open Sans",Arial,sans-serif;color:var(--text)}
.abs{position:absolute}
.raleway{font-family:"Raleway",Arial,sans-serif}

/* header */
.site-header{position:absolute;left:0;top:0;width:1200px;height:91px;background:var(--white)}
.brand{left:99px;top:14px;display:flex;align-items:center;gap:12px}
.brand-mark{width:46px;height:46px;border:3px solid var(--navy);border-radius:50%}
.brand-name{font-family:"Raleway",Arial,sans-serif;font-weight:700;font-size:30px;color:var(--navy)}
.social-top{left:645px;top:14px;display:flex;gap:8px}
.social-top span{width:28px;height:28px;border-radius:50%;background:var(--navy)}
.social-top span:nth-child(3){background:#c8312b}
.social-top span:nth-child(4){background:#7a5b48}
.phone{left:795px;top:14px;display:flex;align-items:center;gap:10px;font-weight:600;font-size:17px;color:#333}
.btn-involved{left:978px;top:13px;width:122px;height:35px;background:var(--blue);color:#fff;font-weight:700;font-size:12px;display:flex;align-items:center;justify-content:center;border-radius:2px;letter-spacing:.3px}
.main-nav{left:330px;top:56px;display:flex;font-family:"Raleway",Arial,sans-serif;font-weight:600;font-size:15px;color:#222}
.main-nav a{color:inherit;text-decoration:none;position:absolute;white-space:nowrap}
.main-nav a.active{color:var(--green)}

/* hero */
.hero{left:0;top:91px;width:1200px;height:428px;background:linear-gradient(90deg,#3b3d42 0%,#55575c 30%,#8f8c8f 55%,#c9c4c6 75%,#7b5e72 100%);overflow:hidden}
.hero-title{left:99px;top:82px;font-family:"Raleway",Arial,sans-serif;font-weight:800;font-size:32px;line-height:49px;color:#fff;letter-spacing:.5px}
.btn-green{background:var(--green);color:#fff;font-weight:700;font-size:14px;display:flex;align-items:center;justify-content:center;border-radius:2px}
.hero-cta{left:99px;top:298px;width:250px;height:42px}
.slider-dots{left:1050px;top:392px;display:flex;gap:6px}
.slider-dots span{width:9px;height:9px;border-radius:50%;background:rgba(255,255,255,.55)}
.slider-dots span:first-child{background:#fff}

/* welcome */
.section-title{font-family:"Raleway",Arial,sans-serif;font-weight:700;font-size:25px;color:var(--ink);text-align:center;width:1200px;left:0}
.welcome-title{top:560px}
.welcome-intro{left:200px;top:612px;width:800px;text-align:center;font-size:12.5px;line-height:25px;color:#666}
.feature{width:240px;text-align:center;top:686px}
.feature svg{display:block;margin:0 auto}
.feature h3{font-family:"Raleway",Arial,sans-serif;font-weight:700;font-size:16px;color:var(--ink);margin-top:20px}
.feature p{font-size:12.5px;line-height:18px;color:#777;margin-top:10px}
.read-more{font-weight:700;font-size:12.5px;color:var(--green);letter-spacing:.3px}
.feature .read-more{display:block;margin-top:14px}

/* process */
.process{left:0;top:997px;width:1200px;height:396px;background:var(--blue)}
.process-title{top:38px;color:#fff}
.step{width:240px;text-align:center;color:#fff;font-weight:600;font-size:15px;line-height:23px;top:271px}

/* why */
.why-title{left:99px;top:1472px;font-family:"Raleway",Arial,sans-serif;font-weight:700;font-size:26px;color:var(--ink)}
.why-list{left:99px;top:1530px;list-style:none}
.why-list li{display:flex;align-items:center;gap:16px;height:41px;font-size:13px;color:#555}
.why-more{left:99px;top:1784px}
.app-shots{left:654px;top:1425px;width:483px;height:418px;background:linear-gradient(135deg,#eceff2,#d6dbe2)}

/* reports */
.reports{left:0;top:1881px;width:1200px;height:436px;background:var(--dark)}
.reports-visual{left:0;top:0;width:631px;height:436px;background:linear-gradient(100deg,#2d2d2d 0%,#5a5a5a 30%,#9a9a9a 55%,#3c3c3c 80%,#2a2a2a 100%)}
.reports-title{left:701px;top:36px;font-family:"Raleway",Arial,sans-serif;font-weight:700;font-size:24px;color:#fff}
.reports-intro{left:701px;top:76px;width:420px;font-size:13px;line-height:25px;color:#ddd}
.report-item{left:701px;width:440px}
.report-item h4{display:flex;align-items:center;gap:16px;font-family:"Raleway",Arial,sans-serif;font-weight:600;font-size:18px;color:#fff}
.report-item p{font-size:12.5px;color:#ccc;margin:8px 0 0 38px}
.reports-more{left:701px;top:373px}

/* partners */
.partners-title{top:2352px}
.partner{top:2404px;width:155px;height:72px;border:1px solid #ddd;background:#fff;display:flex;align-items:center;justify-content:center}
.partner span{display:block;width:110px;height:30px;border-radius:3px;background:#d9dde3}
.carousel-arrow{top:2428px}

/* footer */
.footer-rule{left:0;top:2527px;width:1200px;height:5px;background:var(--green)}
.site-footer{left:0;top:2532px;width:1200px;height:312px;background:var(--footer)}
.footer-brand{left:133px;top:52px;width:119px;height:119px;border:3px solid #fff;border-radius:50%;display:flex;align-items:center;justify-content:center;font-family:"Raleway",Arial,sans-serif;font-weight:700;font-size:34px;color:#fff}
.footer-col{top:35px}
.footer-col h5{font-family:"Raleway",Arial,sans-serif;font-weight:700;font-size:15px;color:#fff;margin-bottom:9px}
.footer-col a{display:block;font-size:12px;line-height:23px;color:#bbb;text-decoration:none}
.footer-divider{left:99px;top:239px;width:1002px;height:1px;background:#333}
.copyright{left:99px;top:266px;font-size:12px;color:#ccc}
.social-foot{left:959px;top:258px;display:flex;gap:8px}
.social-foot span{width:32px;height:32px;border:2px solid #fff;border-radius:50%}
</style>
</head>
<body>

<header class="site-header">
  <div class="abs brand"><span class="brand-mark"></span><span class="brand-name">RV7</span></div>
  <div class="abs social-top"><span></span><span></span><span></span><span></span></div>
  <div class="abs phone">
    <svg width="28" height="28" viewBox="0 0 28 28"><circle cx="14" cy="14" r="12.5" fill="none" stroke="#8cc63f" stroke-width="2"/><path d="M10 8.5c.6-.6 1.4-.5 1.8.2l1 1.8c.3.6.2 1.2-.3 1.6l-.8.7c.6 1.4 1.6 2.5 3 3.2l.7-.8c.4-.5 1.1-.6 1.6-.2l1.8 1.1c.7.4.8 1.2.2 1.8l-.9.9c-.8.8-2.1 1-3.1.5-3-1.5-5.2-3.8-6.6-6.8-.5-1-.2-2.2.6-3z" fill="#8cc63f"/></svg>
    555-014-2270
  </div>
  <div class="abs btn-involved">GET INVOLVED</div>
  <nav class="abs main-nav" style="left:0;top:58px">
    <a class="active" style="left:330px">Home</a>
    <a style="left:424px">About us</a>
    <a style="left:542px">Services</a>
    <a style="left:654px">Emergency Plan</a>
    <a style="left:827px">Resources</a>
    <a style="left:955px">Contact Us</a>
  </nav>
  <svg class="abs" style="left:1088px;top:58px" width="18" height="18" viewBox="0 0 18 18"><circle cx="7.5" cy="7.5" r="5.5" fill="none" stroke="#222" stroke-width="2.2"/><path d="M11.5 11.5l5 5" stroke="#222" stroke-width="2.4" stroke-linecap="round"/></svg>
</header>

<section class="abs hero">
  <div class="abs" style="left:0;top:0;width:1200px;height:428px" role="img" aria-label="Emergency team meeting around a whiteboard with charts in a conference room"></div>
  <svg class="abs" style="left:0;top:0" width="1200" height="428" viewBox="0 0 1200 428">
    <polygon points="470,0 410,0 300,428 360,428" fill="#2a63b1"/>
    <polygon points="520,0 470,0 360,428 410,428" fill="rgba(20,30,50,.35)"/>
  </svg>
  <h1 class="abs hero-title">EMERGENCY -<br>COMMAND,<br>CONTROL &amp;<br>CO-ORDINATION</h1>
  <div class="abs btn-green hero-cta">MAKE AN EMERGENCY PLAN</div>
  <div class="abs slider-dots"><span></span><span></span><span></span></div>
</section>

<h2 class="abs section-title welcome-title">Welcome to Emergency - Command, Control &amp; Co-ordination</h2>
<p class="abs welcome-intro">The product is focused on Preparing for an incident using Volunteer and Resource management and then responding to an incident with Incident Management, Team Management, Task Management and Communication Management.</p>

<div class="abs feature" style="left:90px">
  <svg width="120" height="134" viewBox="0 0 64 72"><path d="M32 3C22 9 12 11 4 11V34C4 52 17 63 32 69 47 63 60 52 60 34V11C52 11 42 9 32 3Z" fill="#fff" stroke="#1d3e8a" stroke-width="2.4"/><path d="M19 35l26-12-8 24-6-7-5 5v-7z" fill="#8cc63f"/><path d="M31 40l14-17" stroke="#fff" stroke-width="1"/></svg>
  <h3>Incident Management</h3>
  <p>At vero eos et accusamus et iusto dignissimos ducimus qui blanditiis pra esentium voluptatum delen</p>
  <span class="read-more">READ MORE &gt;&gt;</span>
</div>
<div class="abs feature" style="left:350px">
  <svg width="120" height="134" viewBox="0 0 64 72"><path d="M32 3C22 9 12 11 4 11V34C4 52 17 63 32 69 47 63 60 52 60 34V11C52 11 42 9 32 3Z" fill="#fff" stroke="#1d3e8a" stroke-width="2.4"/><g fill="#8cc63f"><circle cx="32" cy="27" r="4"/><circle cx="22" cy="29" r="3.2"/><circle cx="42" cy="29" r="3.2"/><path d="M25 44c0-6 3-10 7-10s7 4 7 10z"/><path d="M16 43c0-5 2.5-8 6-8 2 0 3 1 3.5 2-1.5 2-2 4-2 6z"/><path d="M48 43c0-5-2.5-8-6-8-2 0-3 1-3.5 2 1.5 2 2 4 2 6z"/></g></svg>
  <h3>Team Management</h3>
  <p>At vero eos et accusamus et iusto dignissimos ducimus qui blanditiis pra esentium voluptatum delen</p>
  <span class="read-more">READ MORE &gt;&gt;</span>
</div>
<div class="abs feature" style="left:610px">
  <svg width="120" height="134" viewBox="0 0 64 72"><path d="M32 3C22 9 12 11 4 11V34C4 52 17 63 32 69 47 63 60 52 60 34V11C52 11 42 9 32 3Z" fill="#fff" stroke="#1d3e8a" stroke-width="2.4"/><g fill="none" stroke="#8cc63f"><circle cx="28" cy="35" r="6" stroke-width="4"/><circle cx="28" cy="35" r="9.5" stroke-width="3" stroke-dasharray="3 3"/><circle cx="41" cy="27" r="3.5" stroke-width="3"/><circle cx="41" cy="27" r="6" stroke-width="2.4" stroke-dasharray="2 2"/></g></svg>
  <h3>Task Management</h3>
  <p>At vero eos et accusamus et iusto dignissimos ducimus qui blanditiis pra esentium voluptatum delen</p>
  <span class="read-more">READ MORE &gt;&gt;</span>
</div>
<div class="abs feature" style="left:870px">
  <svg width="120" height="134" viewBox="0 0 64 72"><path d="M32 3C22 9 12 11 4 11V34C4 52 17 63 32 69 47 63 60 52 60 34V11C52 11 42 9 32 3Z" fill="#fff" stroke="#1d3e8a" stroke-width="2.4"/><g fill="none" stroke="#8cc63f" stroke-width="3"><ellipse cx="29" cy="30" rx="11" ry="7.5"/><path d="M23 36l-3 6 7-4"/><path d="M38 36c5 0 8 2.5 8 5.5 0 1.5-1 3-2.5 4l1.5 4-5-2.5"/></g></svg>
  <h3>Communication Management</h3>
  <p>At vero eos et accusamus et iusto dignissimos ducimus qui blanditiis pra esentium voluptatum delen</p>
  <span class="read-more">READ MORE &gt;&gt;</span>
</div>

<section class="abs process">
  <h2 class="abs section-title process-title">The Process Of RV7</h2>
  <svg class="abs" style="left:0;top:0" width="1200" height="396" viewBox="0 0 1200 396">
    <g stroke="#b9c9e3" stroke-width="3" fill="none">
      <path d="M302 178h60M354 170l8 8-8 8"/>
      <path d="M567 178h62M621 170l8 8-8 8"/>
      <path d="M832 178h62M886 170l8 8-8 8"/>
    </g>
    <g fill="#fff" stroke="#fff" stroke-width="4">
      <circle cx="205" cy="178" r="74" fill="none"/>
      <circle cx="470" cy="178" r="74" fill="none"/>
      <circle cx="735" cy="178" r="74" fill="none"/>
      <circle cx="999" cy="178" r="74" fill="none"/>
    </g>
    <g fill="#fff"><circle cx="205" cy="178" r="70"/><circle cx="470" cy="178" r="70"/><circle cx="735" cy="178" r="70"/><circle cx="999" cy="178" r="70"/></g>
    <!-- globe -->
    <circle cx="205" cy="178" r="27" fill="#8cc63f"/>
    <path d="M191 166c6 2 8 7 5 11 4 3 2 9 -2 10M214 156c-3 6 2 9 6 8M206 200c1-6 6-8 10-6" stroke="#fff" stroke-width="3" fill="none"/>
    <!-- dots ring -->
    <g fill="#8cc63f"><circle cx="470" cy="150" r="5"/><circle cx="490" cy="158" r="4.5"/><circle cx="498" cy="178" r="4"/><circle cx="490" cy="198" r="3.5"/><circle cx="470" cy="206" r="3.5"/><circle cx="450" cy="198" r="4"/><circle cx="442" cy="178" r="4.5"/><circle cx="450" cy="158" r="5"/></g>
    <!-- gears -->
    <g fill="none" stroke="#8cc63f"><circle cx="726" cy="184" r="9" stroke-width="6"/><circle cx="726" cy="184" r="16" stroke-width="5" stroke-dasharray="4.5 3.5"/><circle cx="749" cy="164" r="5" stroke-width="4"/><circle cx="749" cy="164" r="10" stroke-width="4" stroke-dasharray="3.5 2.5"/></g>
    <!-- document -->
    <path d="M983 150h24l11 11v45h-35z" fill="#8cc63f"/><path d="M1007 150v11h11" fill="#d9ecc0"/><g stroke="#fff" stroke-width="3"><path d="M990 172h21M990 181h21M990 190h21"/></g>
    <!-- number badges -->
    <g fill="#fff" stroke="#2a63b1" stroke-width="3"><circle cx="277" cy="111" r="20"/><circle cx="542" cy="111" r="20"/><circle cx="807" cy="111" r="20"/><circle cx="1071" cy="111" r="20"/></g>
    <g font-family="Open Sans, Arial, sans-serif" font-weight="700" font-size="17" fill="#222" text-anchor="middle"><text x="277" y="117">1</text><text x="542" y="117">2</text><text x="807" y="117">3</text><text x="1071" y="117">4</text></g>
  </svg>
  <p class="abs step" style="left:85px">Access to either the web, mobile or both the interfaces</p>
  <p class="abs step" style="left:350px">Preparing for an incident using Volunteer &amp; Resource management</p>
  <p class="abs step" style="left:615px">Then responding to an incident with Incident, Team, Task, Communication Management</p>
  <p class="abs step" style="left:879px">Once a situation is handled, the application provides complete reporting</p>
</section>

<h2 class="abs why-title">Why adopt RV7</h2>
<ul class="abs why-list">
  <li><svg width="16" height="16" viewBox="0 0 16 16"><circle cx="8" cy="8" r="8" fill="#1d3e8a"/><path d="M4.5 8.2l2.3 2.3 4.7-4.7" stroke="#fff" stroke-width="2" fill="none"/></svg>Easy system to register volunteers</li>
  <li><svg width="16" height="16" viewBox="0 0 16 16"><circle cx="8" cy="8" r="8" fill="#1d3e8a"/><path d="M4.5 8.2l2.3 2.3 4.7-4.7" stroke="#fff" stroke-width="2" fill="none"/></svg>Accurate identification of number of CERT Volunteers available to help in an incident</li>
  <li><svg width="16" height="16" viewBox="0 0 16 16"><circle cx="8" cy="8" r="8" fill="#1d3e8a"/><path d="M4.5 8.2l2.3 2.3 4.7-4.7" stroke="#fff" stroke-width="2" fill="none"/></svg>Efficient Communication mechanism to reach out to the volunteers via SMS</li>
  <li><svg width="16" height="16" viewBox="0 0 16 16"><circle cx="8" cy="8" r="8" fill="#1d3e8a"/><path d="M4.5 8.2l2.3 2.3 4.7-4.7" stroke="#fff" stroke-width="2" fill="none"/></svg>Rich graphical visualization of Incidents &amp; Damages associated with the incidents</li>
  <li><svg width="16" height="16" viewBox="0 0 16 16"><circle cx="8" cy="8" r="8" fill="#1d3e8a"/><path d="M4.5 8.2l2.3 2.3 4.7-4.7" stroke="#fff" stroke-width="2" fill="none"/></svg>Easy Management and Tracking of resources associated</li>
  <li><svg width="16" height="16" viewBox="0 0 16 16"><circle cx="8" cy="8" r="8" fill="#1d3e8a"/><path d="M4.5 8.2l2.3 2.3 4.7-4.7" stroke="#fff" stroke-width="2" fill="none"/></svg>Capture Notes and pictures about situations being handled</li>
</ul>
<span class="abs read-more why-more">READ MORE &gt;&gt;</span>
<div class="abs app-shots" role="img" aria-label="Three smartphones showing the RV7 mobile app: to-do list, volunteer menu and notifications screens"></div>

<section class="abs reports">
  <div class="abs reports-visual" role="img" aria-label="Smartphone in a green case showing an incident map with damage markers, over a black and white photo of modern building architecture"></div>
  <h2 class="abs reports-title">Reports Console</h2>
  <p class="abs reports-intro">City Officials and Emergency Management Officials can get access to instant statistics on</p>
  <div class="abs report-item" style="top:148px">
    <h4><svg width="20" height="20" viewBox="0 0 20 20"><circle cx="10" cy="10" r="10" fill="#8cc63f"/><path d="M5.5 10.2l3 3 6-6" stroke="#fff" stroke-width="2.4" fill="none"/></svg>Incident Management</h4>
    <p>At vero eos et accusamus et iusto odio dignissimos ducimus</p>
  </div>
  <div class="abs report-item" style="top:224px">
    <h4><svg width="20" height="20" viewBox="0 0 20 20"><circle cx="10" cy="10" r="10" fill="#8cc63f"/><path d="M5.5 10.2l3 3 6-6" stroke="#fff" stroke-width="2.4" fill="none"/></svg>Volunteer Management</h4>
    <p>At vero eos et accusamus et iusto odio dignissimos ducimus</p>
  </div>
  <div class="abs report-item" style="top:301px">
    <h4><svg width="20" height="20" viewBox="0 0 20 20"><circle cx="10" cy="10" r="10" fill="#8cc63f"/><path d="M5.5 10.2l3 3 6-6" stroke="#fff" stroke-width="2.4" fill="none"/></svg>Damage Assessment</h4>
    <p>At vero eos et accusamus et iusto odio dignissimos ducimus</p>
  </div>
  <span class="abs read-more reports-more">READ MORE &gt;&gt;</span>
</section>

<h2 class="abs section-title partners-title">Our Partners</h2>
<svg class="abs carousel-arrow" style="left:98px" width="16" height="24" viewBox="0 0 16 24"><path d="M12 2L3 12l9 10" stroke="#888" stroke-width="2.5" fill="none"/></svg>
<div class="abs partner" style="left:182px"><span></span></div>
<div class="abs partner" style="left:353px"><span></span></div>
<div class="abs partner" style="left:523px"><span></span></div>
<div class="abs partner" style="left:694px"><span></span></div>
<div class="abs partner" style="left:863px"><span></span></div>
<svg class="abs carousel-arrow" style="left:1086px" width="16" height="24" viewBox="0 0 16 24"><path d="M4 2l9 10-9 10" stroke="#888" stroke-width="2.5" fill="none"/></svg>

<div class="abs footer-rule"></div>
<footer class="abs site-footer">
  <div class="abs footer-brand">RV7</div>
  <div class="abs footer-col" style="left:320px"><h5>About us</h5><a>Our Story</a><a>Team</a><a>Newsletters</a><a>Contact</a><a>Jobs</a><a>Help Us Grow</a></div>
  <div class="abs footer-col" style="left:463px"><h5>Products</h5><a>Crewline Projects</a><a>Crewline Desk</a><a>Crewline Chat</a></div>
  <div class="abs footer-col" style="left:626px"><h5>Links</h5><a>Desktop Timer App</a><a>Cloud Suite for Business</a><a>Tablet App</a><a>Handset App</a><a>Mobile App</a></div>
  <div class="abs footer-col" style="left:819px"><h5>Resources</h5><a>Roadmap &amp; Updates</a><a>Security</a><a>Privacy Policy</a><a>Terms of Service</a><a>Webinars</a><a>Free for Startups</a></div>
  <div class="abs footer-col" style="left:978px"><h5>Legal</h5><a>Certified Trainers</a><a>Crewline</a><a>Developer Zone</a><a>Referral Program</a><a>Refund Policy</a><a>Login</a></div>
  <div class="abs footer-divider"></div>
  <p class="abs copyright">Copyrights © 2016, RV7. All rights reserved.</p>
  <div class="abs social-foot"><span></span><span></span><span></span><span></span></div>
</footer>

</body>
</html>
```